Business card design Needed for new logo / Construction business, home extensions and new builds

We need a business card design using our new logo files which i will attach to this project :)

We are a small construction business specialising in home extensions, new builds and property development. We are very ambitious and would appreciate professional and elegant designs for our new business card.

Very serious about using the services on MakerQuarry and recently acquired our new logo from here :)

Please get involved, i will feedback when i can as i am very busy but can respond daily, thanks

Target Market(s)

People that want to build onto their houses, new building developments or adding too their existing property

Industry/Entity Type

Construction

Contact Information for Business Card

Renwick Tolliver Construction, Lionel Ashby (Managing Director), Tel 07822254961, email - info@renwick-tolliver, www.renwick-tolliver.co.uk

Colors

Designer to choose colors to be used in the design.

Requirements
Must have
• I like a deep grey on the back please. A lot of you have provided black from and back, try mixing things up a little. The black looks cool 😎 Thanks

```html
<!DOCTYPE html>
<html lang="en">
<head>
<meta charset="utf-8">
<title>Renwick Tolliver Construction – Business Card</title>
<link rel="stylesheet" href="https://fonts.googleapis.com/css2?family=Cinzel:wght@600;700&family=Lato:wght@400;700&display=swap">
<style>
  :root {
    --page: #141414;
    --card-dark: #1c1c1c;
    --gold-deep: #b97c14;
    --gold-mid: #e3b45a;
    --gold-light: #fcd88e;
    --silver-light: #e6e8ea;
    --silver-dark: #8d9196;
    --ink: #121212;
    --brand-gold: #d8a63e;
  }
  html, body {
    margin: 0;
    padding: 0;
    width: 1200px;
    height: 1200px;
    overflow: hidden;
    background: var(--page);
  }
  .canvas {
    position: relative;
    width: 1200px;
    height: 1200px;
  }
  .card {
    position: absolute;
    left: 250px;
    width: 700px;
    height: 400px;
    border-radius: 20px;
    overflow: hidden;
    background: var(--card-dark);
  }
  .card--front { top: 170px; }
  .card--back { top: 631px; }
  .front-shape {
    position: absolute;
    inset: 0;
    width: 700px;
    height: 400px;
  }
  .holder {
    position: absolute;
    left: 37px;
    top: 38px;
    color: var(--ink);
  }
  .holder__name {
    margin: 0;
    font-family: "Cinzel", "Times New Roman", serif;
    font-weight: 700;
    font-size: 35px;
    line-height: 40px;
    letter-spacing: 0.5px;
  }
  .holder__role {
    margin: 0;
    font-family: "Lato", Arial, sans-serif;
    font-size: 20px;
    line-height: 26px;
  }
  .holder__rule {
    position: absolute;
    left: 37px;
    top: 119px;
    width: 72px;
    height: 2px;
    background: var(--ink);
  }
  .contact {
    position: absolute;
    left: 37px;
    top: 138px;
    margin: 0;
    padding: 0;
    list-style: none;
    font-family: "Lato", Arial, sans-serif;
    font-size: 18px;
    letter-spacing: 0.6px;
    color: var(--ink);
  }
  .contact__item {
    display: flex;
    align-items: flex-start;
    min-height: 30px;
    line-height: 30px;
  }
  .contact__icon {
    width: 17px;
    height: 17px;
    margin: 6px 11px 0 0;
    flex: none;
    fill: var(--ink);
  }
  .brand {
    position: absolute;
    font-family: "Cinzel", "Times New Roman", serif;
    font-weight: 600;
    color: var(--brand-gold);
    text-align: center;
    margin: 0;
  }
  .brand--front {
    left: 384px;
    top: 142px;
    width: 290px;
    font-size: 22px;
    line-height: 30px;
    letter-spacing: 1px;
  }
  .brand--back {
    left: 0;
    top: 130px;
    width: 700px;
    font-size: 40px;
    line-height: 54px;
    letter-spacing: 2px;
  }
  .back-web {
    position: absolute;
    left: 0;
    top: 338px;
    width: 700px;
    margin: 0;
    text-align: center;
    font-family: "Lato", Arial, sans-serif;
    font-size: 15px;
    letter-spacing: 2.6px;
    color: var(--brand-gold);
  }
</style>
</head>
<body>
<main class="canvas">

  <section class="card card--front" aria-label="Business card front">
    <svg class="front-shape" viewBox="0 0 700 400" aria-hidden="true">
      <defs>
        <linearGradient id="goldFace" x1="0" y1="0" x2="1" y2="0">
          <stop offset="0" stop-color="var(--gold-mid)"/>
          <stop offset="0.33" stop-color="var(--gold-light)"/>
          <stop offset="0.6" stop-color="var(--gold-mid)"/>
          <stop offset="0.95" stop-color="var(--gold-deep)"/>
        </linearGradient>
        <linearGradient id="silverEdge" x1="0" y1="0" x2="0" y2="1">
          <stop offset="0" stop-color="var(--silver-dark)"/>
          <stop offset="0.5" stop-color="var(--silver-light)"/>
          <stop offset="1" stop-color="var(--silver-dark)"/>
        </linearGradient>
      </defs>
      <polygon points="0,0 463,0 268,195 473,400 0,400" fill="url(#goldFace)"/>
      <polyline points="484,0 286,195 490,400" fill="none" stroke="url(#silverEdge)" stroke-width="9"/>
    </svg>

    <div class="holder">
      <h1 class="holder__name">LIONEL ASHBY</h1>
      <p class="holder__role">Founder &amp; CEO</p>
    </div>
    <div class="holder__rule"></div>

    <ul class="contact">
      <li class="contact__item">
        <svg class="contact__icon" viewBox="0 0 24 24"><path d="M12 1a8 8 0 0 0-8 8c0 6 8 14 8 14s8-8 8-14a8 8 0 0 0-8-8zm0 11a3 3 0 1 1 0-6 3 3 0 0 1 0 6z"/></svg>
        <span>Your Address, City<br>State, Zip 1235</span>
      </li>
      <li class="contact__item">
        <svg class="contact__icon" viewBox="0 0 24 24"><path d="M6.6 10.8a15 15 0 0 0 6.6 6.6l2.2-2.2c.3-.3.7-.4 1-.2 1.1.4 2.3.6 3.6.6.6 0 1 .4 1 1V20c0 .6-.4 1-1 1A17 17 0 0 1 3 4c0-.6.4-1 1-1h3.5c.6 0 1 .4 1 1 0 1.3.2 2.5.6 3.6.1.3 0 .7-.2 1z"/></svg>
        <span>(123) 456-7890</span>
      </li>
      <li class="contact__item">
        <svg class="contact__icon" viewBox="0 0 24 24"><path d="M7 1h10a2 2 0 0 1 2 2v18a2 2 0 0 1-2 2H7a2 2 0 0 1-2-2V3a2 2 0 0 1 2-2zm0 3v14h10V4zm5 15.5a1.2 1.2 0 1 0 0 2.4 1.2 1.2 0 0 0 0-2.4z"/></svg>
        <span>(231) 456-7890</span>
      </li>
      <li class="contact__item">
        <svg class="contact__icon" viewBox="0 0 24 24"><path d="M6 2h12v6H6zM3 9h18a2 2 0 0 1 2 2v7h-4v4H5v-4H1v-7a2 2 0 0 1 2-2zm4 7v4h10v-4zm-4-5v5h2v-2h14v2h2v-5z"/></svg>
        <span>(312) 456-7890</span>
      </li>
      <li class="contact__item">
        <svg class="contact__icon" viewBox="0 0 24 24"><path d="M1 5h22v14H1zm2 2v.4l9 6 9-6V7zm0 2.8V17h18V9.8l-9 6z"/></svg>
        <span>office@yourwebsite.com</span>
      </li>
      <li class="contact__item">
        <svg class="contact__icon" viewBox="0 0 24 24"><path d="M12 1a11 11 0 1 0 0 22 11 11 0 0 0 0-22zm-1 19.9A9 9 0 0 1 3.2 10L8 15v1a2 2 0 0 0 2 2v2.9zm6.9-2.5A2 2 0 0 0 16 17h-1v-3a1 1 0 0 0-1-1H8v-2h2a1 1 0 0 0 1-1V8h2a2 2 0 0 0 2-2v-.4a9 9 0 0 1 2.9 12.8z"/></svg>
        <span>www.yourwebsite.com</span>
      </li>
    </ul>

    <p class="brand brand--front">RENWICK TOLLIVER<br>CONSTRUCTION</p>
  </section>

  <section class="card card--back" aria-label="Business card back">
    <p class="brand brand--back">RENWICK TOLLIVER<br>CONSTRUCTION</p>
    <p class="back-web">WWW.RENWICKTOLLIVERCONSTRUCTION.COM</p>
  </section>

</main>
</body>
</html>
```